KDWB Business Card

Looking for a business card design to incorporate our branding. We want to only use the colors listing in the Branding Package (attached).
Updates

Target Market(s)

People who need their phone or device fixed.

Industry/Entity Type

Electronics

Contact Information for Business Card

Please use:

Brightwick Gadget Clinic LLC
4810 E Harlow Ridge Rd
Suite 417
San Antonio, TX 78163

Marcus Delgrove, Store Manager

(210) 555-0147

Requirements
Must have
• Must include the colors that are contained within the Branding Package PDF file.

```html
<!DOCTYPE html>
<html lang="en">
<head>
<meta charset="utf-8">
<title>Brightwick Gadget Clinic – Business Card</title>
<link rel="stylesheet" href="https://fonts.googleapis.com/css2?family=Montserrat:wght@400;500&display=swap">
<style>
  :root {
    --stage: #2b2e30;
    --card: #94b6ba;
    --orange: #f05527;
    --yellow: #fcbb3d;
    --lime: #d3dc57;
    --ink: #474c52;
  }
  * { margin: 0; padding: 0; box-sizing: border-box; }
  html, body { width: 1200px; height: 1200px; overflow: hidden; }
  body {
    background: var(--stage);
    font-family: "Montserrat", sans-serif;
    position: relative;
  }
  .card {
    position: absolute;
    left: 120px;
    width: 960px;
    height: 549px;
    background: var(--card);
    overflow: hidden;
  }
  .card--front { top: 40px; }
  .card--back { top: 611px; }
  .card__shapes { position: absolute; inset: 0; width: 100%; height: 100%; }
  .brand {
    position: absolute;
    left: 70px;
    top: 240px;
    display: flex;
    align-items: center;
    gap: 18px;
    max-width: 540px;
  }
  .brand__mark {
    width: 72px;
    height: 72px;
    border-radius: 16px;
    background: var(--orange);
    flex: none;
  }
  .brand__name {
    font-size: 32px;
    font-weight: 400;
    color: var(--orange);
    letter-spacing: 0.3px;
    white-space: nowrap;
  }
  .person { position: absolute; left: 270px; top: 150px; }
  .person__name {
    font-size: 34px;
    font-weight: 500;
    color: var(--orange);
    text-transform: uppercase;
    letter-spacing: 1.5px;
  }
  .person__role { font-size: 23px; color: var(--ink); margin-top: 4px; }
  .contact {
    position: absolute;
    left: 230px;
    top: 330px;
    list-style: none;
  }
  .contact__item {
    display: flex;
    align-items: center;
    gap: 22px;
    font-size: 24px;
    line-height: 1.3;
    color: var(--ink);
    margin-bottom: 22px;
  }
  .contact__icon { width: 50px; height: 50px; flex: none; }
</style>
</head>
<body>

<section class="card card--front" aria-label="Card front">
  <svg class="card__shapes" viewBox="0 0 960 549" aria-hidden="true">
    <polygon fill="var(--orange)" points="640,0 700,0 700,300 635,255"/>
    <polygon fill="var(--yellow)" points="700,0 765,0 740,549 700,549 700,300 730,320"/>
    <polygon fill="var(--lime)" points="765,0 772,0 747,549 740,549"/>
    <polygon fill="var(--orange)" points="772,0 800,0 960,420 960,549 747,549"/>
    <polygon fill="var(--lime)" points="0,300 110,420 40,549 0,549"/>
  </svg>
  <div class="brand">
    <div class="brand__mark"></div>
    <div class="brand__name">Brightwick Gadget Clinic</div>
  </div>
</section>

<section class="card card--back" aria-label="Card back">
  <svg class="card__shapes" viewBox="0 0 960 549" aria-hidden="true">
    <polygon fill="var(--orange)" points="0,0 225,0 50,549 0,549"/>
    <polygon fill="var(--lime)" points="225,0 232,0 57,549 50,549"/>
    <polygon fill="var(--yellow)" points="160,210 195,245 100,549 57,549"/>
    <polygon fill="var(--lime)" points="835,0 960,0 960,280 940,280 800,70"/>
  </svg>

  <div class="person">
    <div class="person__name">Marcus Delgrove</div>
    <div class="person__role">Store Manager</div>
  </div>

  <ul class="contact">
    <li class="contact__item">
      <svg class="contact__icon" viewBox="0 0 50 50" aria-hidden="true">
        <circle cx="25" cy="25" r="25" fill="var(--orange)"/>
        <path d="M25 12a9 9 0 0 0-9 9c0 7 9 17 9 17s9-10 9-17a9 9 0 0 0-9-9z" fill="none" stroke="var(--yellow)" stroke-width="2.5"/>
        <circle cx="25" cy="21" r="3.2" fill="var(--yellow)"/>
      </svg>
      <span>4810 E Harlow Ridge Rd<br>Suite 417, San Antonio, TX 78163</span>
    </li>
    <li class="contact__item">
      <svg class="contact__icon" viewBox="0 0 50 50" aria-hidden="true">
        <circle cx="25" cy="25" r="25" fill="var(--orange)"/>
        <path d="M17 14l5 0 2 7-3 2a14 14 0 0 0 7 7l2-3 7 2 0 5c0 2-2 3-4 3-10-1-19-10-19-19 0-2 1-4 3-4z" fill="none" stroke="var(--yellow)" stroke-width="2.3" stroke-linejoin="round"/>
      </svg>
      <span>(210) 555-0147</span>
    </li>
    <li class="contact__item">
      <svg class="contact__icon" viewBox="0 0 50 50" aria-hidden="true">
        <circle cx="25" cy="25" r="25" fill="var(--orange)"/>
        <rect x="13" y="17" width="24" height="17" rx="2" fill="none" stroke="var(--yellow)" stroke-width="2.3"/>
        <path d="M13 18l12 9 12-9" fill="none" stroke="var(--yellow)" stroke-width="2.3"/>
      </svg>
      <span>mdelgrove@brightwickmail.com</span>
    </li>
  </ul>
</section>

</body>
</html>
```